Design Project - Finance Website (Only need PSD)

UPDATED PROJECT (Now only PSD needed)
Need a Wordpress design for a company called "Corvale Lending Partners". The company provides finance for corporate clients, businesses and property developers. The design should be business like with appealing colours that communicate trust. I have uploaded a banner and logo to be incorporated or feel free to design something better if you think you can.
** I now only need the PSD
** I want something that is actually designed rather than from a template.
Thanks
Updates
The website will be used for lead generation so the contact form with adjustable fields in the Wordpress backend should be fairly prominent on the page.
I have uploaded a banner and logo for the site. None of the designs I have seen so far were good enough so the first decent design using the new banner and logo provided will win the job. I do not want just a template that has been cut and paste from somewhere else, I want decent design. If anyone provides a decent design then I will give an extra bonus of $150.
Reason: I have uploaded a banner and logo for the site. None of the designs I have seen so far were good enough so the first decent design using the new banner and logo provided will win the job. I do not want just a template that has been cut and paste from somewhere else, I want decent design. If anyone provides a decent design then I will give an extra bonus of $150.
Thanks
Target Market(s)
Business owners & property developers
Industry/Entity Type
Finance
Requirements
Must have
- Contact form on home page that can be altered through the back end eg. ability to add or remove fields. Widgetised sidebars.
Nice to have
- Widgetised footer.

```html
<!DOCTYPE html>
<html lang="en">
<head>
<meta charset="utf-8">
<title>Corvale Lending Partners</title>
<link rel="stylesheet" href="https://fonts.googleapis.com/css2?family=Source+Sans+3:wght@400;600&family=PT+Sans+Narrow&display=swap">
<style>
:root{
  --brand-blue:#0f5db3;
  --brand-blue-light:#1c6abd;
  --heading-blue:#1a5fb0;
  --canvas-grey:#e6e6e8;
  --panel-grey:#f4f4f4;
  --line-grey:#d4d4d4;
  --text-dark:#3a3a3a;
  --white:#ffffff;
}
*{margin:0;padding:0;box-sizing:border-box}
html,body{width:1200px;height:1086px;overflow:hidden}
body{position:relative;background:var(--canvas-grey);font-family:"Source Sans 3",sans-serif;color:var(--text-dark)}
.abs{position:absolute}
.header-band{left:0;top:0;width:1200px;height:258px;background:var(--brand-blue);border-bottom:2px solid #8a8f97}
.search-box{left:710px;top:16px;width:230px;height:23px;background:var(--white);border-radius:12px;border:1px solid #c8d3e0;font-size:11px;color:var(--brand-blue);padding:4px 11px}
.search-box svg{position:absolute;right:8px;top:4px}
.social-dot{top:16px;width:21px;height:21px;border-radius:4px;background:#4a8bd2}
.site-name{left:178px;top:49px;color:var(--white);font-size:25px;letter-spacing:.2px}
.main-nav{left:455px;top:54px;width:558px;height:28px;background:var(--white);border-radius:8px;display:flex;box-shadow:0 2px 3px rgba(0,0,0,.25)}
.main-nav a{flex:1;text-align:center;line-height:28px;font-size:12px;color:var(--brand-blue);text-decoration:none;border-left:1px solid #b9c8da}
.main-nav a:first-child{border-left:none}
.hero{left:174px;top:110px;width:844px;height:311px;background:linear-gradient(180deg,#5a5fa8 0%,#2f3d8a 45%,#1c2a4e 80%,#2a3050 100%);border:1px solid #b7bfcc;box-shadow:0 14px 14px -6px rgba(0,0,0,.35)}
.hero-points{left:201px;top:138px;color:var(--white);font-family:"PT Sans Narrow",sans-serif;font-size:18px;line-height:27.5px}
.slider-dots{left:525px;top:403px;width:162px;height:30px;background:rgba(150,155,170,.85);border:1px solid #c9ccd4;border-radius:8px;display:flex;justify-content:center;align-items:center;gap:7px}
.slider-dots span{width:12px;height:12px;border-radius:50%;background:var(--white);border:2px solid #2d63b5}
.slider-dots span.active{background:#e2461c;border-color:#f08a5e}
.section-title{top:466px;color:var(--heading-blue);font-family:"PT Sans Narrow",sans-serif;font-size:19px}
.title-bar{top:470px;width:8px;height:25px;background:var(--brand-blue)}
.news-arrows{left:425px;top:470px;display:flex;gap:3px}
.news-arrows span{width:18px;height:17px;background:#c5cbd4;border:1px solid #98a2b0;display:flex;align-items:center;justify-content:center}
.info-panel{left:176px;top:497px;width:840px;height:200px;border-radius:22px;background:linear-gradient(180deg,var(--panel-grey) 0%,var(--panel-grey) 50%,var(--white) 50%);border:1px solid #dcdcdc}
.panel-divider{top:497px;width:1px;height:200px;background:var(--line-grey)}
.news-thumb{left:205px;width:51px;height:47px;background:linear-gradient(180deg,#c9cfd6,#4a4f57);border:1px solid #999}
.news-text{left:269px;width:186px;font-size:11px;line-height:17px;text-align:justify}
.case-photo{left:503px;top:511px;width:241px;height:84px;background:linear-gradient(120deg,#b8bec6,#6f8a6f 55%,#c9cdd2)}
.case-text{left:503px;top:603px;width:241px;font-size:11px;line-height:16.6px;text-align:justify}
.read-more{left:503px;top:671px;width:241px;text-align:right;font-size:11px;color:var(--heading-blue)}
.form-field{left:787px;width:198px;height:30px;border:1px solid #c6c6c6;border-radius:15px;background:var(--white);font-size:11px;line-height:28px;padding-left:17px}
.newsletter-box{left:791px;top:643px;width:13px;height:12px;background:#c9c9c9}
.newsletter-label{left:816px;top:641px;font-size:11px}
.submit-btn{left:926px;top:667px;width:59px;height:21px;border-radius:11px;background:var(--brand-blue);color:var(--white);font-size:11px;text-align:center;line-height:21px;box-shadow:0 2px 3px rgba(0,0,0,.3)}
.welcome{left:0;top:713px;width:1200px;height:213px;background:var(--white)}
.welcome-title{left:197px;top:730px;color:var(--heading-blue);font-family:"PT Sans Narrow",sans-serif;font-size:19px}
.welcome-rule{left:198px;top:760px;width:797px;border-top:1px dashed #888}
.welcome-text{left:198px;top:771px;width:525px;font-size:12.2px;line-height:22.2px;text-align:justify}
.welcome-photo{left:756px;top:785px;width:239px;height:104px;background:linear-gradient(180deg,#3f4b4e,#8a8a7a 55%,#4b4432)}
.footer{left:0;top:926px;width:1200px;height:160px;background:var(--brand-blue)}
.footer-top{left:0;top:926px;width:1200px;height:73px;background:var(--brand-blue-light)}
.footer-col{top:944px;list-style:none;font-size:12px;line-height:26px;color:var(--white)}
.footer-brand{top:1011px;right:205px;color:var(--white);font-size:18.5px}
.footer-copy{top:1038px;right:205px;color:var(--white);font-size:11px}
</style>
</head>
<body>
<div class="abs header-band"></div>
<div class="abs search-box">Search
  <svg width="14" height="14" viewBox="0 0 14 14"><circle cx="5.5" cy="5.5" r="4" fill="none" stroke="#888" stroke-width="1.5"/><line x1="8.5" y1="8.5" x2="13" y2="13" stroke="#888" stroke-width="2"/></svg>
</div>
<div class="abs social-dot" style="left:962px"></div>
<div class="abs social-dot" style="left:990px"></div>
<div class="abs site-name">Corvale Lending Partners</div>
<nav class="abs main-nav"><a>Home</a><a>About Us</a><a>Services</a><a>Finance</a><a>Real Estate</a><a>Contact Us</a></nav>

<div class="abs hero" role="img" aria-label="Night city skyline with lit office towers"></div>
<div class="abs hero-points">Compare several capital provider rates<br>Access to real estate and hedge funds<br>Optimise your capital returns</div>
<div class="abs slider-dots"><span></span><span></span><span></span><span class="active"></span><span></span><span></span><span></span></div>

<div class="abs section-title" style="left:210px">Latest News</div>
<div class="abs news-arrows">
  <span><svg width="6" height="8"><path d="M5 0L1 4l4 4" fill="none" stroke="#1a4f91" stroke-width="1.6"/></svg></span>
  <span><svg width="6" height="8"><path d="M1 0l4 4-4 4" fill="none" stroke="#1a4f91" stroke-width="1.6"/></svg></span>
</div>
<div class="abs title-bar" style="left:474px"></div>
<div class="abs section-title" style="left:506px">Case Study</div>
<div class="abs title-bar" style="left:764px"></div>
<div class="abs section-title" style="left:786px">Quick Contact</div>

<div class="abs info-panel"></div>
<div class="abs panel-divider" style="left:478px"></div>
<div class="abs panel-divider" style="left:768px"></div>

<div class="abs news-thumb" style="top:515px" role="img" aria-label="Business team photo"></div>
<p class="abs news-text" style="top:520px">Lorem Ipsum is simply dummy text of the printing and typesetting industry.</p>
<div class="abs news-thumb" style="top:576px" role="img" aria-label="Business team photo"></div>
<p class="abs news-text" style="top:582px">Lorem Ipsum is simply dummy text of the printing and typesetting industry.</p>
<div class="abs news-thumb" style="top:636px" role="img" aria-label="Business team photo"></div>
<p class="abs news-text" style="top:640px">Lorem Ipsum is simply dummy text of the printing and typesetting industry.</p>

<div class="abs case-photo" role="img" aria-label="Students in a classroom"></div>
<p class="abs case-text">Lorem Ipsum is simply dummy text of the printing and typesetting industry. Lorem Ipsum has been the industry's standard dummy text ever since the 1500s,</p>
<div class="abs read-more">Read More &gt;&gt;</div>

<div class="abs form-field" style="top:515px">Name</div>
<div class="abs form-field" style="top:555px">E mail Address</div>
<div class="abs form-field" style="top:595px">Phone</div>
<div class="abs newsletter-box"></div>
<div class="abs newsletter-label">Subscribe to Our Newsletter</div>
<div class="abs submit-btn">Submit</div>

<div class="abs welcome"></div>
<div class="abs welcome-title">Welcome to Our Site</div>
<div class="abs welcome-rule"></div>
<p class="abs welcome-text">It is a long established fact that a reader will be distracted by the readable content of a page when looking at its layout. The point of using Lorem Ipsum is that it has a more-or-less normal distribution of letters, as opposed to using 'Content here, content here', making it look like readable English. Many desktop publishing packages and web page editors now use Lorem Ipsum as their default model text, and a search for 'lorem ipsum' will uncover many web sites still in their infancy. Various versions have evolved over the years, sometimes by accident, sometimes on purpose (injected humour and the like).</p>
<div class="abs welcome-photo" role="img" aria-label="Modern glass office building at dusk"></div>

<footer>
<div class="abs footer"></div>
<div class="abs footer-top"></div>
<ul class="abs footer-col" style="left:201px"><li>About Us</li><li>Services</li><li>Finance</li><li>Real Estate</li><li>Contact Us</li></ul>
<ul class="abs footer-col" style="left:339px"><li>About Us</li><li>Services</li><li>Finance</li><li>Real Estate</li><li>Contact Us</li></ul>
<ul class="abs footer-col" style="left:477px"><li>About Us</li><li>Services</li><li>Finance</li><li>Real Estate</li><li>Contact Us</li></ul>
<div class="abs footer-brand">Corvale Lending Partners</div>
<div class="abs footer-copy">Copyrights @ 2012 All Rights Reserved</div>
</footer>
</body>
</html>
```